Building company needs a letterhead design

I'm after a modern but professional letter head.
Must have the below details:
- Logo
- Website - TARVELLGROUP.COM.AU
- Email - INFO@TARVELLGROUP.COM.AU
- Office - 03 57263018
- Mobile number - 0418536294
- ABN - 47 315 962 108
...........................................................................................................................................................................................................................
- Logo
- Office - 03 57263018
- ABN - 47 315 962 108

Target Market(s)

.

Industry/Entity Type

Construction Company

Font styles to use
Sans Serif

Requirements
Must have
• Must have the below details:
• - Logo
• - Website - TARVELLGROUP.COM.AU
• - Email - INFO@TARVELLGROUP.COM.AU
• - Office - 03 57263018
• - Mobile number - 0418536294
• - ABN - 47 315 962 108
Nice to have
• .
Should not have
• .

```html
<!DOCTYPE html>
<html lang="en">
<head>
<meta charset="utf-8">
<title>Tarvell Building Group – Letterhead</title>
<link href="https://fonts.googleapis.com/css2?family=Open+Sans:wght@400;700;800&display=swap" rel="stylesheet">
<style>
  :root {
    --backdrop: #e9e7e3;
    --paper: #ffffff;
    --brand-yellow: #fbb514;
    --brand-grey: #5f5f61;
    --rule-grey: #6d6d6f;
    --text-grey: #555557;
  }
  * { margin: 0; padding: 0; box-sizing: border-box; }
  html, body {
    width: 1186px;
    height: 1200px;
    overflow: hidden;
    background: var(--backdrop);
    font-family: "Open Sans", Arial, sans-serif;
  }
  .letterhead {
    position: absolute;
    left: 211px;
    top: 60px;
    width: 764px;
    height: 1080px;
    background: var(--paper);
    box-shadow: 0 6px 18px rgba(0,0,0,0.18);
  }
  .header-band {
    position: absolute;
    left: 0; top: 0;
    width: 100%;
    height: 62px;
    background: var(--brand-yellow);
  }
  .header-rule {
    position: absolute;
    left: 0; top: 66px;
    width: 100%;
    height: 3px;
    background: var(--rule-grey);
  }
  .brand {
    position: absolute;
    top: 26px;
    left: 50%;
    transform: translateX(-50%);
    background: var(--paper);
    padding: 12px 18px 10px;
    display: flex;
    flex-direction: column;
    align-items: center;
    gap: 8px;
  }
  .brand-square {
    width: 58px;
    height: 58px;
    background: var(--brand-yellow);
  }
  .brand-name {
    font-weight: 800;
    font-size: 15px;
    letter-spacing: 0.06em;
    color: var(--brand-grey);
    text-transform: uppercase;
    white-space: nowrap;
  }
  .contact-footer {
    position: absolute;
    left: 56px;
    bottom: 38px;
    display: flex;
    align-items: center;
    gap: 14px;
    font-size: 11px;
    color: var(--text-grey);
  }
  .contact-item {
    display: flex;
    align-items: center;
    gap: 5px;
  }
  .contact-item svg {
    width: 11px;
    height: 11px;
    fill: var(--brand-yellow);
  }
  .contact-divider {
    width: 1px;
    height: 13px;
    background: #b8b8ba;
  }
</style>
</head>
<body>
  <main class="letterhead">
    <div class="header-band"></div>
    <div class="header-rule"></div>

    <div class="brand">
      <div class="brand-square"></div>
      <div class="brand-name">Tarvell Building Group</div>
    </div>

    <footer class="contact-footer">
      <span class="contact-item">
        <svg viewBox="0 0 12 12" aria-hidden="true"><circle cx="6" cy="6" r="6"/><path d="M4 3.2l1 1.4-.6.7c.4.9 1 1.5 1.9 1.9l.7-.6 1.4 1-.6 1.1C5.8 8.6 3.4 6.2 3 4.2z" fill="#fff"/></svg>
        03 57263018
      </span>
      <span class="contact-item">
        <svg viewBox="0 0 12 12" aria-hidden="true"><rect x="3" y="0.5" width="6" height="11" rx="1.2"/><rect x="4.2" y="2" width="3.6" height="6" fill="#fff"/></svg>
        0418536294
      </span>
      <span class="contact-item">
        <svg viewBox="0 0 12 12" aria-hidden="true"><circle cx="6" cy="6" r="6"/><path d="M3 4h6v4H3z" fill="#fff"/><path d="M3 4l3 2.2L9 4" fill="none" stroke="#fbb514" stroke-width=".8"/></svg>
        info@tarvellgroup.com.au
      </span>
      <span class="contact-item">
        <svg viewBox="0 0 12 12" aria-hidden="true"><circle cx="6" cy="6" r="6"/><circle cx="6" cy="6" r="3.4" fill="none" stroke="#fff" stroke-width=".8"/><path d="M2.6 6h6.8M6 2.6v6.8" stroke="#fff" stroke-width=".8"/></svg>
        www.tarvellgroup.com.au
      </span>
      <span class="contact-divider"></span>
      <span class="contact-item">ABN: 47 315 962 108</span>
    </footer>
  </main>
</body>
</html>
```